Upscale neighbourhood mail campaign requiring 3 postcard designs

I am looking for a series of 3 postcards to be designed. They all must have a common look to them to show they belong to the same company. We are a local real estate company that specializes in an area called Morgan Creek. You can visit our website at www.ashvaleridgehomes.ca to have a peek. I have HD photos I can provide of the area, or include your own ideas/images. The post cards text will be provided and they will be sent as unaddressed admail, meaning there is no need to include areas for postage or mailing addresses. The final design should be clean, recognizable and professional. These cards must have visual impact on the recipients.

COPY for 3 POSTCARDs

POSTCARD 1

FRONT

(included Logo)

Get noticed.
Your home deserves it

BACK

We take finding Buyers for your home very seriously.

Through our unique, Morgan Creek specific website, targeted digital marketing, EXCLUSIVE Buyer incentives and our featured listing promotion, your home is in front of the people that want to see it. People who WANT to live in Morgan Creek.

Visit ashvaleridgehomes.ca to learn more about what we do so your home can GET NOTICED. Your home deserves it.

Colet Varnish- PREC | Pelham Estates LTD | 604-555-0192 | homes@varnish.ca

This communication is not intended to cause or induce breach of an existing agency agreement. Although this information has been received from sources deemed reliable, we assume no responsibility for its accuracy and without offering advice, make this submission to prior sale or lease, change in price or terms, and withdrawal without notice

POSTCARD 2

FRONT

Logo

Get noticed.
Expect the best.

BACK

You deserve the best when it comes to the marketing and exposure of your home, which is why your neighbours choose ashvaleridgehomes.ca to sell their home. Our award winning results combined with our systematized approach to marketing makes selling your home with us a breeze. In addition, you have full access to our dedicated client concierge, in place to ensure your sale is stress free and an overall rewarding experience.

Visit ashvaleridgehomes.ca to learn more about what we do so your home can GET NOTICED. Expect the best.

POSTCARD 3

FRONT

Logo

Get noticed.
Rule the web

BACK

No one promotes your home more than ashvaleridgehomes.ca. Just try us. Type ashvale ridge homes into any internet search browser and see for yourself. We advertise Morgan Creek internationally, in all major Canadian Cities and locally to affluent Buyers who appreciate what Morgan Creek has to offer. No one offers a more specific, targeted approach to getting your home sold.

Visit ashvaleridgehomes.ca to learn more about what we do so your home can GET NOTICED so you can rule the web.

Target Market(s)

Upscale neighbourhood in Surrey BC, Canada called Morgan Creek

Industry/Entity Type

Real Estate

Font styles to use
Other font styles liked:
• Lato

Colors

Designer to choose colors to be used in the design.

Requirements
Must have
• -Clean, impactful and professional looking card
• -Font- Lato
• -Provided Ashvale Ridge Homes logo
• -Check www.ashvaleridgehomes.ca for complimentary color scheme
• -provided Morgan Creek logo on the front
• -provided --CV logo, Pelham Estates logo and medallion crest on the back
• -Disclaimer in small, low-key font/color - "This communication is not intended to cause or induce breach of an existing agency agreement. Although this information has been received from sources deemed reliable, we assume no responsibility for its accuracy and without offering advice, make this submission to prior sale or lease, change in price or terms, and withdrawal without notice"
Nice to have
• -bold images, not 100% necessary though (discretion of designer)
• -impactful front of postcard
Should not have
• -cartoon style drawings
• -areas for postage or mailing addresses (this will be sent as non addressed admail by the local postal courier)

```html
<!DOCTYPE html>
<html lang="en">
<head>
<meta charset="utf-8">
<title>Ashvale Ridge Homes – Postcard 2</title>
<link href="https://fonts.googleapis.com/css2?family=Lato:wght@300;400;700&display=swap" rel="stylesheet">
<style>
  :root {
    --brand-green: #5f6b32;
    --brand-dark: #3f4224;
    --link-green: #5a6a2a;
    --ink: #1d1d1d;
    --muted: #6b6b6b;
    --paper: #ffffff;
    --backdrop: #e6e6e4;
    --sky: #a9c3dc;
    --lawn: #7e9a52;
    --siding: #b9b6ad;
  }
  * { box-sizing: border-box; margin: 0; padding: 0; }
  html, body {
    width: 1041px; height: 1200px; overflow: hidden;
    background: var(--backdrop);
    font-family: 'Lato', sans-serif;
    color: var(--ink);
  }
  .canvas { position: relative; width: 1041px; height: 1200px; }
  .postcard {
    position: absolute; left: 80px; width: 880px;
    background: var(--paper);
    box-shadow: 0 4px 12px rgba(0,0,0,.18);
    overflow: hidden;
  }

  /* Front */
  .postcard--front { top: 18px; height: 574px; }
  .front__photo {
    height: 443px;
    background: linear-gradient(180deg, #f2f2f0 0%, var(--siding) 45%, #8c8a80 70%, var(--lawn) 100%);
  }
  .front__band {
    position: absolute; left: 0; right: 0; bottom: 0; height: 126px;
    background: var(--brand-green); color: #fff;
    display: flex; align-items: center; justify-content: space-between;
    padding: 0 46px 0 29px;
  }
  .front__kicker { font-weight: 300; font-size: 34px; line-height: 1.1; letter-spacing: .5px; }
  .front__headline { font-weight: 400; font-size: 42px; line-height: 1.25; }
  .brand-mark { display: flex; align-items: center; gap: 12px; }
  .brand-mark__square { width: 18px; height: 18px; background: #fff; }
  .brand-mark__name { font-weight: 400; font-size: 24px; letter-spacing: 1.5px; text-transform: uppercase; }

  /* Back */
  .postcard--back { top: 612px; height: 571px; }
  .back__gallery { display: flex; gap: 3px; height: 180px; }
  .back__photo { flex: 1; }
  .back__photo--stone { background: linear-gradient(180deg, #bccfe0 0%, #8e8c8a 50%, #6f8f48 100%); }
  .back__photo--gable { background: linear-gradient(180deg, #e5ecf1 0%, #b3a79c 50%, #6a7f45 100%); }
  .back__photo--ranch { background: linear-gradient(180deg, var(--sky) 0%, #a79c88 50%, #5f8f38 100%); }

  .back__heading {
    margin-top: 15px; height: 43px;
    background: var(--brand-green); color: #fff;
    font-weight: 700; font-size: 18px;
    display: flex; align-items: center; padding-left: 21px;
  }
  .back__body { padding: 18px 21px 0; }
  .back__copy { font-size: 16.3px; line-height: 20.5px; text-align: justify; }
  .back__cta { margin-top: 20px; font-size: 16.3px; }
  .back__cta a { color: var(--link-green); text-decoration: none; font-weight: 700; }

  .back__fine {
    display: flex; justify-content: space-between; align-items: center;
    margin-top: 24px;
  }
  .disclaimer { width: 550px; font-size: 10.2px; line-height: 11.5px; color: var(--muted); }
  .partner-row { display: flex; align-items: center; gap: 22px; }
  .partner--agent { display: flex; align-items: center; gap: 6px; }
  .partner__square { width: 14px; height: 14px; background: #2b3d6b; }
  .partner__name { font-size: 14px; font-weight: 700; color: #2b3d6b; }
  .partner__name--realty { color: var(--ink); }
  .partner--board { width: 40px; height: 40px; border-radius: 50%; background: #bdbdbd; }

  .contact { position: absolute; left: 0; right: 0; bottom: 0; height: 95px; }
  .contact__tab {
    position: absolute; left: 0; top: 0; height: 42px; width: 200px;
    background: var(--brand-dark); color: #fff;
    font-size: 23px; font-weight: 400;
    display: flex; align-items: center; padding-left: 21px;
    clip-path: polygon(0 0, 100% 0, 90% 100%, 0 100%);
  }
  .contact__band {
    position: absolute; left: 0; right: 0; bottom: 0; height: 72px;
    background: var(--brand-green); color: #fff;
    display: flex; align-items: center; padding-left: 21px;
    font-size: 23px;
  }
  .contact__band::before {
    content: ""; position: absolute; left: 0; right: 0; top: 0; height: 0;
  }
</style>
</head>
<body>
<main class="canvas">

  <section class="postcard postcard--front">
    <div class="front__photo" role="img" aria-label="Photo of a new craftsman-style home with white porch columns, stone bases and a row of neighbouring houses"></div>
    <div class="front__band">
      <div class="front__headings">
        <p class="front__kicker">GET NOTICED.</p>
        <h1 class="front__headline">Expect the best.</h1>
      </div>
      <div class="brand-mark">
        <span class="brand-mark__square"></span>
        <span class="brand-mark__name">Ashvale Ridge Homes</span>
      </div>
    </div>
  </section>

  <section class="postcard postcard--back">
    <div class="back__gallery">
      <div class="back__photo back__photo--stone" role="img" aria-label="Photo of a large stone-faced estate home with manicured hedges"></div>
      <div class="back__photo back__photo--gable" role="img" aria-label="Photo of a two-storey gabled home with a white garage door"></div>
      <div class="back__photo back__photo--ranch" role="img" aria-label="Photo of a wide family home under a blue sky with a green lawn"></div>
    </div>

    <h2 class="back__heading">EXPECT THE BEST.</h2>

    <div class="back__body">
      <p class="back__copy">You deserve the best when it comes to the marketing and exposure of your home, which is why your neighbours choose ashvaleridgehomes.ca to sell their home. Our award winning results combined with our systematized approach to marketing makes selling your home with us a breeze. In addition, you have full access to our dedicated client concierge, in place to ensure your sale is stress free and an overall rewarding experience.</p>
      <p class="back__cta">Visit <a href="#">ashvaleridgehomes.ca</a> to learn more about what we do so your home can GET NOTICED.</p>

      <div class="back__fine">
        <p class="disclaimer">This communication is not intended to cause or induce breach of an existing agency agreement. Although this information has been received from sources deemed reliable, we assume no responsibility for its accuracy and without offering advice, make this submission to prior sale or lease, change in price or terms, and withdrawal without notice.</p>
        <div class="partner-row">
          <div class="partner--agent"><span class="partner__square"></span><span class="partner__name">CV</span></div>
          <span class="partner__name partner__name--realty">Pelham Estates</span>
          <span class="partner--board" role="img" aria-label="Real estate board membership badge"></span>
        </div>
      </div>
    </div>

    <footer class="contact">
      <div class="contact__band">Colet Varnish- PREC | Pelham Estates LTD | 604-555-0192 | homes@varnish.ca</div>
      <div class="contact__tab">CONTACT US</div>
    </footer>
  </section>

</main>
</body>
</html>
```